Business Cards Design for the electrical wholesaler: clean bold dynamic :)

We need a business card design that would follow our latest brand guidelines. As an electrical wholesaler we want to bring a fresh look and feel into the industry. The design should be clean bold and dynamic. It should come alive with the renewed energy of our green colour. Our grey colour should keep things balanced and complement the notion of maturity and responsibility. We employ Lato as a corporate font however are not bound by this font and we’re open to interpretation here.

Target Market(s)

Electrical contractors

Industry/Entity Type

Business

Contact Information for Business Card

Logo
Name & Surname: Halyna Dorosh
Job Title: Director of Marketing
Email: halya.dorosh@quillmail.example
Cell phone: XXX.XXX.XXXX
Address: 20517 - 87 Ave. Edmonton, AB, Canada. T6K 4N8
Business Phone: 780.555.0184
Website: www.brovix.example

Font styles to use
Other font styles liked:
• Lato

Requirements
Must have
• Logo & website
Nice to have
• Brand elements - some of them you may find in the attached Brand Guidelines (e.g. three lines on the background signifying "W")

```html
<!DOCTYPE html>
<html lang="en">
<head>
<meta charset="utf-8">
<title>Brovix Business Card</title>
<link href="https://fonts.googleapis.com/css2?family=Work+Sans:wght@400;500&display=swap" rel="stylesheet">
<style>
  :root {
    --backdrop: #151515;
    --card-base: #1c1c1c;
    --card-glow: #3a3a3a;
    --brand-green: #8cc63f;
    --text-light: #f2f2f2;
    --mark-faint: rgba(255,255,255,0.07);
  }
  * { margin: 0; padding: 0; box-sizing: border-box; }
  html, body {
    width: 1200px; height: 897px; overflow: hidden;
    background: var(--backdrop);
    font-family: "Work Sans", Arial, sans-serif;
  }
  .stage { position: relative; width: 1200px; height: 897px; }
  .card {
    position: absolute; left: 304px; width: 594px; height: 338px;
    border-radius: 19px; overflow: hidden;
    background:
      radial-gradient(ellipse 60% 70% at 85% 55%, var(--card-glow) 0%, rgba(58,58,58,0) 70%),
      var(--card-base);
  }
  .card-front { top: 92px; }
  .card-back { top: 470px; }

  .brand { position: absolute; display: flex; align-items: center; color: var(--text-light); font-weight: 500; letter-spacing: -0.01em; line-height: 1; }
  .brand-square { background: var(--brand-green); flex: none; }
  .card-front .brand { left: 34px; top: 32px; font-size: 46px; gap: 12px; }
  .card-front .brand-square { width: 30px; height: 30px; }
  .card-back .brand { left: 50%; top: 50%; transform: translate(-50%, -50%); font-size: 84px; gap: 20px; }
  .card-back .brand-square { width: 54px; height: 54px; }

  .person { position: absolute; right: 36px; top: 34px; text-align: right; }
  .person-name { color: var(--brand-green); font-size: 24px; font-weight: 400; letter-spacing: 0.01em; line-height: 1.2; }
  .person-role { color: var(--text-light); font-size: 15.5px; letter-spacing: 0.03em; line-height: 1.3; }

  .contacts { position: absolute; left: 35px; top: 184px; list-style: none; }
  .contacts li { display: flex; align-items: center; gap: 10px; height: 19px; color: var(--text-light); font-size: 15px; letter-spacing: 0.03em; white-space: nowrap; }
  .contacts svg { width: 11px; height: 11px; flex: none; }
  .address { position: absolute; left: 34px; top: 274px; color: var(--text-light); font-size: 15px; line-height: 19px; letter-spacing: 0.03em; font-style: normal; }

  .brand-watermark { position: absolute; right: 36px; top: 196px; font-size: 92px; line-height: 1.1; font-weight: 500; color: var(--mark-faint); letter-spacing: -0.01em; }
</style>
</head>
<body>
<main class="stage">
  <section class="card card-front" aria-label="Card front">
    <div class="brand-watermark" aria-hidden="true">Brovix</div>
    <div class="brand"><span class="brand-square"></span>Brovix</div>
    <div class="person">
      <p class="person-name">Halyna Dorosh</p>
      <p class="person-role">Director of Marketing</p>
    </div>
    <ul class="contacts">
      <li>
        <svg viewBox="0 0 12 12"><path d="M3 1 L4.6 1.4 L5 3.6 L3.9 4.4 Q5 7 7.6 8.1 L8.4 7 L10.6 7.4 L11 9 Q10 11 8 10.6 Q2 9 1.4 3 Q1.4 1.6 3 1 Z" fill="var(--brand-green)"/></svg>
        780.555.0184
      </li>
      <li>
        <svg viewBox="0 0 12 12"><rect x="3" y="0.8" width="6" height="10.4" rx="1.2" fill="none" stroke="var(--brand-green)" stroke-width="1.2"/><circle cx="6" cy="9.2" r="0.7" fill="var(--brand-green)"/></svg>
        XXX.XXX.XXXX
      </li>
      <li>
        <svg viewBox="0 0 12 12"><rect x="1" y="2.5" width="10" height="7" fill="none" stroke="var(--brand-green)" stroke-width="1.2"/><path d="M1 2.5 L6 6.5 L11 2.5" fill="none" stroke="var(--brand-green)" stroke-width="1.2"/></svg>
        halya.dorosh@quillmail.example
      </li>
      <li>
        <svg viewBox="0 0 12 12" fill="none" stroke="var(--brand-green)" stroke-width="1"><circle cx="6" cy="6" r="4.8"/><ellipse cx="6" cy="6" rx="2" ry="4.8"/><path d="M1.2 6 H10.8 M2 3.6 H10 M2 8.4 H10"/></svg>
        www.brovix.example
      </li>
    </ul>
    <address class="address">20517 87ave<br>T6K4N8 Edmonton, Alberta</address>
  </section>

  <section class="card card-back" aria-label="Card back">
    <div class="brand"><span class="brand-square"></span>Brovix</div>
  </section>
</main>
</body>
</html>
```